Trailer wrap for home remodeling company in Sarasota County Florida

I need a wrap design for an enclosed trailer. I like the idea of adding a picture of a really nice kitchen or bathroom, possibly a before and after.
Matte black background
Must include the below information
Pinecrest Home Remodeling
CGC2871093
941-555–0184
www.pinecresthomeremodeling.example
Bathrooms,Kitchens, Additions, Remodels
Trusted Expertise. Refined Design
Trailer is currently all black
Updates

Designs are not what we are looking for, very busy

Industry/Entity Type

Home Remodeling

Colors
0054AA
0677BA
7BADD7
CADEEF
E8F1F8

Requirements
Must have
• Matte black background

```html
<!DOCTYPE html>
<html lang="en">
<head>
<meta charset="utf-8">
<title>Pinecrest Home Remodeling – Trailer Wrap</title>
<link rel="stylesheet" href="https://fonts.googleapis.com/css2?family=Crimson+Pro:wght@400;700&display=swap">
<style>
  :root {
    --matte-black: #050505;
    --navy: #1a3a8c;
    --navy-deep: #15307a;
    --bright-blue: #1f62d8;
    --white: #ffffff;
    --page: #eef0f3;
    --trim: #b9bdc2;
  }
  * { margin: 0; padding: 0; box-sizing: border-box; }
  html, body { width: 801px; height: 1200px; overflow: hidden; background: var(--page); }
  body { position: relative; font-family: "Crimson Pro", Georgia, serif; color: var(--white); }

  .wrap-panel { position: absolute; overflow: hidden; }
  .wrap-panel svg { position: absolute; inset: 0; display: block; }
  .side-street { left: 30px; top: 30px; width: 740px; height: 340px; }
  .side-curb { left: 30px; top: 405px; width: 740px; height: 340px; }
  .rear-doors { left: 220px; top: 785px; width: 360px; height: 385px; }

  .txt { position: absolute; white-space: nowrap; line-height: 1; }
  .centered { transform: translateX(-50%); text-align: center; }

  .company-name {
    font-family: "Crimson Pro", Georgia, serif;
    font-weight: 400;
    color: var(--white);
    line-height: 1.1;
    letter-spacing: 0;
  }

  .services { list-style: none; }
  .services li { line-height: 1.25; }
  .services li::before { content: "• "; }
  .phone { font-weight: 700; letter-spacing: -0.01em; }
  .web { font-weight: 700; }
  .license { font-weight: 700; font-size: 12px; }
  .tagline { font-weight: 700; line-height: 1.2; }

  .web-pill { background: var(--bright-blue); border-radius: 12px; padding: 2px 12px 4px; }
</style>
</head>
<body>

<!-- Street side: tongue at right -->
<section class="wrap-panel side-street">
  <svg viewBox="0 0 740 340" width="740" height="340" aria-hidden="true">
    <rect width="740" height="340" fill="var(--navy)"/>
    <polygon points="135,0 740,0 740,282 500,282" fill="var(--matte-black)"/>
    <polygon points="112,0 135,0 500,282 470,282" fill="var(--bright-blue)"/>
    <polygon points="470,282 740,282 740,340 545,340" fill="var(--bright-blue)"/>
    <polyline points="0,24 95,24 130,40 460,300 505,340" fill="none" stroke="var(--bright-blue)" stroke-width="10"/>
    <polyline points="0,36 90,36 120,50 440,305 480,340" fill="none" stroke="var(--navy-deep)" stroke-width="4"/>
    <rect x="557" y="67" width="125" height="260" fill="var(--bright-blue)" stroke="var(--trim)" stroke-width="3"/>
    <path d="M156,340 L156,322 C170,286 200,278 298,278 C396,278 426,286 440,322 L440,340 Z" fill="var(--page)"/>
  </svg>
  <ul class="txt services" style="left:43px; top:94px; font-size:20px;">
    <li>Bathrooms</li><li>Kitchens</li><li>Additions</li><li>Remodels</li>
  </ul>
  <div class="txt phone" style="left:43px; top:204px; font-size:31px;">941-555–0184</div>
  <div class="txt web" style="left:43px; top:237px; font-size:20px;">pinecresthomeremodeling.example</div>
  <div class="txt license" style="left:25px; top:313px;">CGC# 2871093</div>

  <div class="txt company-name centered" style="left:420px; top:90px; font-size:34px;">Pinecrest Home<br>Remodeling</div>

  <div class="txt tagline centered" style="left:620px; top:204px; font-size:19px;">Trusted<br>Expertise<br>Refined<br>Design</div>
</section>

<!-- Curb side: tongue at left -->
<section class="wrap-panel side-curb">
  <svg viewBox="0 0 740 340" width="740" height="340" aria-hidden="true">
    <rect width="740" height="340" fill="var(--navy)"/>
    <polygon points="0,0 630,0 262,276 0,276" fill="var(--matte-black)"/>
    <polygon points="0,276 262,276 630,0 668,0 280,300 225,340 0,340" fill="var(--bright-blue)"/>
    <polyline points="740,20 650,20 620,34 300,300 250,340" fill="none" stroke="var(--bright-blue)" stroke-width="10"/>
    <polyline points="740,32 655,32 630,44 318,300 268,340" fill="none" stroke="var(--navy-deep)" stroke-width="4"/>
    <path d="M308,340 L308,322 C322,288 352,280 452,280 C552,280 582,288 596,322 L596,340 Z" fill="var(--page)"/>
  </svg>
  <div class="txt company-name centered" style="left:206px; top:90px; font-size:42px;">Pinecrest Home<br>Remodeling</div>
  <div class="txt web web-pill centered" style="left:206px; top:210px; font-size:15px;">pinecresthomeremodeling.example</div>
  <div class="txt phone" style="left:24px; top:290px; font-size:32px;">941-555–0184</div>

  <div class="txt tagline" style="left:574px; top:141px; font-size:17px; line-height:1.25;">Trusted Expertise<br>Refined Design</div>
  <ul class="txt services" style="left:574px; top:188px; font-size:19px;">
    <li>Bathrooms</li><li>Kitchens</li><li>Additions</li><li>Remodels</li>
  </ul>
  <div class="txt license" style="left:615px; top:307px;">CGC# 2871093</div>
</section>

<!-- Rear doors -->
<section class="wrap-panel rear-doors">
  <svg viewBox="0 0 360 385" width="360" height="385" aria-hidden="true">
    <rect width="360" height="385" fill="var(--navy)"/>
    <polyline points="0,28 22,28" fill="none" stroke="var(--bright-blue)" stroke-width="8"/>
    <polyline points="338,28 360,28" fill="none" stroke="var(--bright-blue)" stroke-width="8"/>
    <path d="M22,0 L338,0 L300,136 Q292,160 268,160 L92,160 Q68,160 60,136 Z" fill="var(--matte-black)" stroke="var(--bright-blue)" stroke-width="8"/>
  </svg>
  <div class="txt company-name centered" style="left:180px; top:60px; font-size:30px;">Pinecrest Home<br>Remodeling</div>

  <div class="txt" style="left:24px; top:217px; font-size:15px; line-height:1.35;">• Bathrooms &nbsp;• Kitchens<br>• Additions &nbsp;&nbsp;• Remodels</div>
  <div class="txt" style="left:208px; top:217px; font-size:15px; line-height:1.35; border-left:1px solid var(--white); padding-left:8px;">Trusted Expertise<br>Refined Design</div>
  <div class="txt phone" style="left:24px; top:285px; font-size:34px;">941-555–0184</div>
  <div class="txt web" style="left:24px; top:324px; font-size:17px;">pinecresthomeremodeling.example</div>
</section>

</body>
</html>
```